The Linen Loft Co

We need a business card design for our wardrobe company.
Please visit our website www.gentlelinenlofts.com to get an idea of who we are.

```html
<!DOCTYPE html>
<html lang="en">
<head>
<meta charset="utf-8">
<title>The Linen Loft Co – Business Card</title>
<link href="https://fonts.googleapis.com/css2?family=Lato:wght@400;700&display=swap" rel="stylesheet">
<style>
  :root {
    --backdrop: #2b2b2b;
    --card: #1d1d1d;
    --ink: #ffffff;
    --ink-soft: #b4b4b4;
    --rule: #6a6a6a;
  }
  * { margin: 0; padding: 0; box-sizing: border-box; }
  html, body {
    width: 1200px; height: 866px; overflow: hidden;
    background: var(--backdrop);
    font-family: "Lato", sans-serif;
    color: var(--ink);
  }
  .sheet {
    width: 1200px; height: 866px;
    display: flex; align-items: center; justify-content: center; gap: 48px;
  }
  .card {
    position: relative;
    width: 540px; height: 310px;
    background: var(--card);
    box-shadow: 0 10px 28px rgba(0,0,0,.55);
  }
  .brand { display: flex; align-items: center; gap: 14px; }
  .brand-square {
    width: 34px; height: 34px;
    border: 2px solid var(--ink);
  }
  .brand-name {
    font-weight: 700; font-size: 17px; letter-spacing: .5px;
    text-transform: uppercase; line-height: 1.1;
  }
  .brand-tagline { font-size: 13px; margin-top: 4px; }

  .card-front .brand { position: absolute; left: 210px; top: 48px; }
  .person { position: absolute; left: 26px; top: 118px; }
  .person-name { font-weight: 700; font-size: 18px; text-transform: uppercase; letter-spacing: .3px; }
  .person-role { font-size: 13px; color: var(--ink-soft); margin-top: 2px; }
  .divider {
    position: absolute; left: 190px; right: 40px; top: 160px;
    height: 1px; background: var(--rule);
  }
  .contacts { position: absolute; left: 26px; top: 176px; list-style: none; }
  .contacts li {
    display: flex; align-items: center; gap: 8px;
    font-size: 13px; line-height: 20px; color: #e6e6e6;
  }
  .contacts svg { width: 11px; height: 11px; fill: var(--ink); flex: none; }
  .address {
    position: absolute; right: 40px; bottom: 30px;
    text-align: right; font-size: 14px; line-height: 20px; color: var(--ink-soft);
    font-style: normal;
  }

  .card-back { display: flex; align-items: center; justify-content: center; }
  .card-back .brand-name { font-size: 19px; }
  .card-back .brand-tagline { font-size: 14px; }
</style>
</head>
<body>
<main class="sheet">
  <section class="card card-front" aria-label="Card front">
    <div class="brand">
      <span class="brand-square"></span>
      <div>
        <div class="brand-name">The Linen Loft Co</div>
        <div class="brand-tagline">Folding it all in Order</div>
      </div>
    </div>
    <div class="person">
      <div class="person-name">Daniel Harper</div>
      <div class="person-role">Managing Director</div>
    </div>
    <div class="divider"></div>
    <ul class="contacts">
      <li><svg viewBox="0 0 12 12" aria-hidden="true"><path d="M2 1h2.5l1 2.5-1.5 1a6 6 0 0 0 3.5 3.5l1-1.5 2.5 1V10a1 1 0 0 1-1 1A9 9 0 0 1 1 2a1 1 0 0 1 1-1z"/></svg>0207 555 0148</li>
      <li><svg viewBox="0 0 12 12" aria-hidden="true"><path d="M0 2h12v8H0z M0.6 2.4 6 6.5l5.4-4.1" fill="#fff" stroke="#1d1d1d" stroke-width="1"/></svg>info@gentlelinenlofts.com</li>
      <li><svg viewBox="0 0 12 12" aria-hidden="true"><circle cx="6" cy="6" r="5.5"/><path d="M0.5 6h11M6 0.5c-2.5 3-2.5 8 0 11M6 0.5c2.5 3 2.5 8 0 11" stroke="#1d1d1d" stroke-width=".8" fill="none"/></svg>www.gentlelinenlofts.com</li>
    </ul>
    <address class="address">
      Marlow House, 42 Weaver Street<br>London EC2A 4QP
    </address>
  </section>

  <section class="card card-back" aria-label="Card back">
    <div class="brand">
      <span class="brand-square"></span>
      <div>
        <div class="brand-name">The Linen Loft Co</div>
        <div class="brand-tagline">Folding it all in Order</div>
      </div>
    </div>
  </section>
</main>
</body>
</html>
```